Local Flower Farm Needs Business Card Design

I need business cards designed for a flower farm based in Eudora, Kansas.
Business Info:
We are a local cut flower farm located in Eudora, Kansas, founded by Corinne Haldwick. What started as a passion for agriculture and search for more joy in daily life has blossomed into a small business dedicated to providing the community with beautiful, fresh, and sustainable flowers. We specialize in local, seasonal blooms, ensuring that every petal reflects the care and dedication we pour into our craft. Our mission is to deliver the highest quality flowers directly to our customers through local farmers markets and to florists who share our commitment to sustainability. Join us in celebrating the beauty of nature, one bloom at a time!
Contact Details:
Corinne Haldwick
Owner
Phone 913-555-0147
Facebook: Rosalind Thorpe Gardens
Instagram: @RosalindThorpeGardens
Website: RosalindThorpeGardens.example
Target Market(s)
Wholesale to Florists and Direct to Consumer via Farmers Market
Industry/Entity Type
Florist, Farm
Contact Information for Business Card
Name, Contact Info, Logo
Look and feel
Each slider illustrates characteristics of the customer's brand and the style your logo design should communicate.

```html
<!DOCTYPE html>
<html lang="en">
<head>
<meta charset="UTF-8">
<title>Rosalind Thorpe Gardens – Business Card</title>
<link href="https://fonts.googleapis.com/css2?family=Lora:ital,wght@0,400;0,500;1,400&family=Libre+Baskerville:wght@400;700&display=swap" rel="stylesheet">
<style>
  :root {
    --ink: #0f2e33;
    --ink-soft: #3c4f52;
    --muted: #6f7a7c;
    --paper: #ffffff;
    --paper-shade: #f1f1f1;
    --backdrop: #e6e4e0;
    --art-tone: #dfe5e5;
  }
  * { margin: 0; padding: 0; box-sizing: border-box; }
  html, body {
    width: 1200px; height: 900px; overflow: hidden;
    background: var(--backdrop);
  }
  .canvas {
    position: relative; width: 1200px; height: 900px;
    display: flex; flex-direction: column; align-items: center; justify-content: center; gap: 48px;
  }
  .card {
    position: relative; width: 640px; height: 366px;
    background: linear-gradient(135deg, var(--paper) 0%, var(--paper-shade) 100%);
    box-shadow: 0 10px 24px rgba(0,0,0,0.18);
    overflow: hidden;
  }
  .card__band {
    position: absolute; left: 0; right: 0; bottom: 0; height: 16px;
    background: var(--ink);
  }
  .floral-art {
    position: absolute; left: 0; top: 40px; width: 210px; height: 310px;
    background: linear-gradient(160deg, var(--art-tone) 0%, rgba(223,229,229,0.35) 100%);
    border-radius: 0 110px 0 0;
  }
  .seal {
    position: absolute; top: 22px; right: 44px; width: 138px; height: 138px;
    border: 1.5px solid var(--ink); border-radius: 50%;
    display: flex; align-items: center; justify-content: center; text-align: center;
    font-family: "Lora", serif; font-weight: 500; font-size: 16px; line-height: 1.25;
    color: var(--ink); letter-spacing: 0.06em; text-transform: uppercase;
  }
  .tagline {
    position: absolute; right: 40px; bottom: 62px; width: 460px;
    text-align: right;
    font-family: "Lora", serif; font-size: 15px; line-height: 1.6;
    color: var(--ink-soft);
  }
  .owner {
    position: absolute; left: 200px; bottom: 28px;
  }
  .owner__role {
    font-family: "Lora", serif; font-size: 15px; line-height: 1.2; color: var(--muted);
  }
  .owner__name {
    font-family: "Libre Baskerville", serif; font-weight: 700; font-size: 20px; line-height: 1.3;
    color: var(--ink); letter-spacing: 0.02em; text-transform: uppercase;
  }
  .contact-list {
    position: absolute; right: 40px; top: 172px; list-style: none;
    font-family: "Lora", serif; font-size: 15px; color: var(--ink-soft);
  }
  .contact-list li {
    display: flex; align-items: center; justify-content: flex-end; gap: 8px;
    height: 26px; white-space: nowrap;
  }
  .contact-icon {
    width: 17px; height: 17px; flex: none;
  }
</style>
</head>
<body>
<main class="canvas">

  <section class="card card--back">
    <div class="floral-art" role="img" aria-label="Line drawing of wildflower stems with buds and open blooms"></div>
    <div class="seal">Rosalind<br>Thorpe<br>Gardens</div>
    <p class="tagline">We specialize in local, seasonal blooms, ensuring that every petal reflects the care and dedication we pour into our craft. Join us in celebrating the beauty of nature, one bloom at a time!</p>
    <div class="card__band"></div>
  </section>

  <section class="card card--front">
    <div class="floral-art" role="img" aria-label="Line drawing of wildflower stems with buds and open blooms"></div>
    <div class="seal">Rosalind<br>Thorpe<br>Gardens</div>
    <ul class="contact-list">
      <li>913-555-0147
        <svg class="contact-icon" viewBox="0 0 24 24" aria-hidden="true"><circle cx="12" cy="12" r="12" fill="var(--ink)"/><path d="M8.5 6.5l2 2.5-1.2 1.4c.8 1.7 2 2.9 3.6 3.6l1.4-1.2 2.5 2-1.2 2c-4.5-.3-8.6-4.4-8.9-8.9z" fill="#fff"/></svg>
      </li>
      <li>Rosalind Thorpe Gardens
        <svg class="contact-icon" viewBox="0 0 24 24" aria-hidden="true"><circle cx="12" cy="12" r="12" fill="var(--ink)"/></svg>
      </li>
      <li>@RosalindThorpeGardens
        <svg class="contact-icon" viewBox="0 0 24 24" aria-hidden="true"><circle cx="12" cy="12" r="12" fill="var(--ink)"/></svg>
      </li>
      <li>RosalindThorpeGardens.example
        <svg class="contact-icon" viewBox="0 0 24 24" aria-hidden="true"><circle cx="12" cy="12" r="11" fill="none" stroke="var(--ink)" stroke-width="1.8"/><ellipse cx="12" cy="12" rx="4.5" ry="11" fill="none" stroke="var(--ink)" stroke-width="1.5"/><path d="M1 12h22M3 7h18M3 17h18" stroke="var(--ink)" stroke-width="1.3"/></svg>
      </li>
    </ul>
    <div class="owner">
      <p class="owner__role">Owner</p>
      <p class="owner__name">Corinne Haldwick</p>
    </div>
    <div class="card__band"></div>
  </section>

</main>
</body>
</html>
```